Velvet Harbor Snout Sticks - our own unique product line of cotton swabs

We have something now that we are not too happy with. Looking to create a label for a line of cotton swabs that we have created and designed to clean your nose from mucus and boogers. The logo that i have so far for the packaging is the white background with the black silhouette nose (attached). We need something that can do well in the retail/consumer market. Our website address (even though it is not live yet) should be listed somewhere on the label....
www.VelvetHarborGoods.example ( we sell pillows, but we have other product lines)
We would also like to see a brief description on how to correctly use the nose pick on the back side of the label. The description on how to use should read " insert cotton nose pick into nostril and give it a few counter clock wise twirls or till you feel mucus/debris latch onto the cotton. You may need to repeat the process and use more than one nose pick to achieve desired result."
As well as a warning mentioning : "Never insert plastic end of nose pick into any part of your body. Be careful and use with caution."
Also for you to know, the cotton is made from 100% natural cotton, the cotton head itself is thick and highly absorbent making it a pleasure to use. There are 50 nose picks per pack.
We're fine with keeping it simple and not making the packaging too busy, however we're open to your ideas and designs! I have given you the most important information relevant to the project. If there are any questions or something is not clear enough please kindly message me.

Requirements
Must have
• professional looking
clean looking
not busy
Should not have
• words clumping together making it appear as too much text in one area
too much text clumped together on the design

```html
<!DOCTYPE html>
<html lang="en">
<head>
<meta charset="utf-8">
<title>Velvet Harbor Snout Sticks – Label</title>
<link rel="stylesheet" href="https://fonts.googleapis.com/css2?family=Montserrat:wght@400;500;600;700;800&family=Courgette&display=swap">
<style>
  :root {
    --teal: #3fbfb5;
    --teal-soft: #c9ece9;
    --grey: #6b7276;
    --grey-light: #e3e6e7;
    --border: #9aa0a3;
    --white: #ffffff;
  }
  * { box-sizing: border-box; margin: 0; padding: 0; }
  html, body { width: 1200px; height: 589px; overflow: hidden; background: var(--white); }
  body { position: relative; font-family: 'Montserrat', sans-serif; color: var(--grey); }

  .front-label {
    position: absolute; left: 40px; top: 84px; width: 560px; height: 420px;
    border: 1px solid var(--border); background: var(--white); overflow: hidden;
  }
  .brand-name {
    position: absolute; left: 46px; top: 62px;
    font-size: 40px; font-weight: 500; color: var(--grey); letter-spacing: 0.5px;
  }
  .seal {
    position: absolute; left: 393px; top: 30px; width: 108px; height: 108px;
    border-radius: 50%; background: var(--teal);
  }
  .nose-art {
    position: absolute; left: 30px; top: 150px; width: 82px; height: 190px;
    border-radius: 40px 10px 40px 30px;
    background: linear-gradient(160deg, var(--grey-light), #cfd4d6);
  }
  .material-line {
    position: absolute; left: 140px; top: 180px;
    font-size: 17px; font-weight: 700; letter-spacing: 2.5px;
  }
  .title-band {
    position: absolute; left: 117px; top: 207px; width: 443px; height: 69px;
    background: var(--teal); color: var(--white); text-align: center;
  }
  .title-band .product {
    display: block; margin-top: 4px;
    font-size: 42px; font-weight: 800; letter-spacing: 4px; line-height: 46px;
  }
  .title-band .tagline {
    display: block; font-size: 11px; font-weight: 700; letter-spacing: 0.4px;
  }
  .question {
    position: absolute; left: 200px; top: 282px;
    font-family: 'Courgette', cursive; font-size: 24px; color: var(--grey);
  }
  .swab-art {
    position: absolute; left: 130px; top: 314px; width: 378px; height: 8px;
    border-radius: 4px; background: linear-gradient(90deg, var(--grey-light), var(--grey));
  }
  .count {
    position: absolute; left: 400px; top: 328px; text-align: center; line-height: 1;
  }
  .count .number { display: block; font-size: 48px; font-weight: 800; }
  .count .unit { display: block; font-size: 18px; font-weight: 700; }
  .website {
    position: absolute; left: 48px; top: 366px;
    font-size: 15px; font-weight: 500; color: var(--teal); letter-spacing: 1px;
  }

  .usage-label {
    position: absolute; left: 640px; top: 178px; width: 520px; height: 232px;
    border: 1px solid var(--border); background: var(--white); text-align: center;
  }
  .usage-heading {
    position: absolute; left: 0; right: 0; top: 11px;
    display: flex; align-items: center; justify-content: center; gap: 6px;
    font-size: 15px; font-weight: 700; color: var(--teal); letter-spacing: 0.5px;
  }
  .usage-heading::before, .usage-heading::after {
    content: ""; width: 78px; border-top: 3px dotted var(--teal);
  }
  .steps {
    position: absolute; left: 0; right: 0; top: 34px; height: 68px;
    display: flex; align-items: center; justify-content: center; gap: 10px;
  }
  .step-art {
    width: 66px; height: 66px; border-radius: 50%;
    border: 3px solid var(--teal); background: var(--teal-soft);
  }
  .step-arrow { width: 20px; height: 14px; }
  .instructions {
    position: absolute; left: 40px; right: 40px; top: 108px;
    font-size: 13.5px; line-height: 16.5px; color: var(--grey);
  }
  .warning {
    position: absolute; left: 49px; top: 178px; width: 422px; height: 38px;
    border-radius: 8px; background: var(--teal); color: var(--white);
    font-size: 13px; line-height: 16px; padding-top: 3px;
  }
</style>
</head>
<body>
  <section class="front-label" aria-label="Front label">
    <div class="brand-name">Velvet Harbor</div>
    <div class="seal" role="img" aria-label="Natural cotton, highly absorbent seal"></div>
    <div class="nose-art" role="img" aria-label="Line drawing of a nose in profile"></div>
    <p class="material-line">100% NATURAL COTTON</p>
    <div class="title-band">
      <span class="product">SNOUT STICKS</span>
      <span class="tagline">CLEAN YOUR NOSE FROM MUCUS AND BOOGERS</span>
    </div>
    <p class="question">How do you pick your nose?</p>
    <div class="swab-art" role="img" aria-label="Cotton swab drawing"></div>
    <p class="count"><span class="number">50</span><span class="unit">count</span></p>
    <p class="website">www.VelvetHarborGoods.example</p>
  </section>

  <section class="usage-label" aria-label="Back label">
    <h2 class="usage-heading">HOW TO USE</h2>
    <div class="steps">
      <div class="step-art" role="img" aria-label="Step 1: swab entering nostril"></div>
      <svg class="step-arrow" viewBox="0 0 20 14"><path d="M0 5h11V0l9 7-9 7V9H0z" fill="var(--teal)"/></svg>
      <div class="step-art" role="img" aria-label="Step 2: swab twirled counter clockwise"></div>
      <svg class="step-arrow" viewBox="0 0 20 14"><path d="M0 5h11V0l9 7-9 7V9H0z" fill="var(--teal)"/></svg>
      <div class="step-art" role="img" aria-label="Step 3: swab removed from nose"></div>
    </div>
    <p class="instructions">Insert cotton nose pick into nostril and give it a few counter clock wise twirls or till you feel mucus/debris latch onto the cotton. You may need to repeat the process and use more than one nose pick to achieve desired result.</p>
    <p class="warning">Never insert plastic end of nose pick into any part of<br>your body. Be careful and use with caution.</p>
  </section>
</body>
</html>
```